Residential real estate home builder in west texas

We need a website design for our home building business based in west Texas called Birch Hollow homes. We build new construction for potential homeowners in Amarillo. Currently we do not have any completed construction, but we have floor plans and architectural drawings of the front elevation. The website would need to be able to properly advertise a architectural drawing, floor plans, and descriptive content at the initial phase. The website will need to be simple but professional with generic picture content.
The website will need the ability to be updated in the future for the additions of home pictures, and video content and virtual tours of the homes.

Target Market(s)

Potential Home buyers

Industry/Entity Type

Real Estate

Number of Pages Required

5+ page

Font styles to use
Sans Serif

Colors
f37122
757575

Requirements
Must have
• Web design must be simple and easy to navigate. There is not much picture content, so it will need to be simple.
• 5 pages:
• Home, Available homes, Available floor plans, guide to ownership, Contact
• The website will need the ability to be updated in the future for the additions of pictures, and video content of the homes when they are built. ( A virtual tour).
Nice to have
• I would like to see a modern and cohesive design. Contact information at the bottom of each page.
Should not have
• A Black background

```html
<!DOCTYPE html>
<html lang="en">
<head>
<meta charset="utf-8">
<title>Birch Hollow Homes</title>
<link href="https://fonts.googleapis.com/css2?family=Open+Sans:ital,wght@0,300;0,400;0,600;0,700;1,400&display=swap" rel="stylesheet">
<style>
:root{
  --orange:#f37122;
  --grey:#757575;
  --grey-dark:#5f5f5f;
  --footer:#6f6f6f;
  --footer-base:#5e5e5e;
  --text:#555;
  --muted:#888;
  --light:#f2f2f2;
  --line:#e2e2e2;
  --white:#fff;
}
*{box-sizing:border-box;margin:0;padding:0}
html,body{width:1200px;height:2378px;overflow:hidden}
body{position:relative;font-family:"Open Sans",Arial,sans-serif;color:var(--text);background:var(--white)}
.abs{position:absolute}
a{color:inherit;text-decoration:none}

.topbar{left:0;top:0;width:1200px;height:40px;background:var(--grey);color:#eee;font-size:12px}
.topbar .item{position:absolute;top:12px;display:flex;align-items:center;gap:7px;white-space:nowrap}
.topbar .search{position:absolute;right:98px;top:0;width:42px;height:40px;background:var(--grey-dark);display:flex;align-items:center;justify-content:center}

.header{left:0;top:40px;width:1200px;height:92px;background:var(--white);box-shadow:0 1px 3px rgba(0,0,0,.06)}
.logo{position:absolute;left:98px;top:26px;width:192px;text-align:center;color:var(--grey);font-weight:600;white-space:nowrap}
.logo .name{font-size:25px;letter-spacing:-.3px;line-height:28px}
.logo .sub{font-size:12px;letter-spacing:6px;line-height:16px}
.nav{position:absolute;right:98px;top:38px;display:flex;gap:33px;font-size:14px;color:#666}
.nav .active{color:#333;font-weight:600;position:relative}
.nav .active::after{content:"";position:absolute;left:-10px;right:-10px;top:38px;height:2px;background:var(--orange)}
.nav .active::before{content:"";position:absolute;left:50%;top:40px;margin-left:-5px;border:5px solid transparent;border-top-color:var(--orange)}

.hero{left:0;top:132px;width:1200px;height:421px;background:radial-gradient(ellipse at 50% 40%,#f4f4f4 0%,#e6e6e6 60%,#d9d9d9 100%)}
.play{left:572px;top:322px;width:56px;height:56px;border-radius:50%;background:#4a4a4a}
.caption{left:449px;top:394px;width:332px;height:32px;background:rgba(90,90,90,.75);color:#fff;font-size:22px;font-weight:300;text-align:center;line-height:32px}

.section-title{width:1200px;left:0;text-align:center;font-size:28px;font-weight:300;color:var(--grey)}
.section-title b{font-weight:600;color:#666}
.section-title::after{content:"";display:block;width:38px;height:2px;background:var(--orange);margin:8px auto 0}

.intro{left:179px;top:640px;width:846px;font-size:12.5px;line-height:21px;text-align:center;color:#666}
.btn{display:inline-block;border:1px solid var(--orange);color:var(--orange);font-size:12px;text-align:center;background:#fff}
.btn.solid{background:var(--orange);color:#fff}

.service{top:840px;width:450px;height:361px;border:1px solid #f3a571;background:#fff}
.service .media{margin:0;height:244px}
.service h3{position:absolute;left:20px;top:258px;font-size:17px;font-weight:600;color:#555}
.service h3 span{font-weight:400}
.service .arrow{position:absolute;right:20px;top:262px}
.service p{position:absolute;left:20px;top:294px;width:410px;font-size:12px;line-height:21px;color:#777}

.posts{left:0;top:1249px;width:1200px;height:428px;background:linear-gradient(160deg,#f6f6f6,#ececec)}
.post{top:1330px;width:325px}
.post .media{height:165px}
.post h4{font-size:13px;font-weight:400;letter-spacing:1px;color:#555;margin:14px 0 0 14px}
.post h4 b{font-weight:700}
.post p{font-size:11.5px;line-height:20px;color:#777;margin:10px 14px 0 14px;text-align:justify}
.post .btn{position:absolute;top:282px;left:14px;width:84px;height:29px;line-height:27px;font-size:11px}

.block-title{font-size:27px;font-weight:300;color:var(--grey);text-transform:uppercase}
.block-title b{font-weight:400}
.clients{left:120px;top:1772px;width:464px;height:168px;display:grid;grid-template-columns:repeat(3,1fr);grid-template-rows:repeat(2,1fr);gap:3px}
.client{border:1px solid var(--line);display:flex;align-items:center;justify-content:center;gap:8px;font-size:16px;color:#666}
.client .dot{width:10px;height:10px;background:#666}
.testimonial{left:631px;top:1780px;width:460px;font-size:11.5px;font-style:italic;line-height:20px;color:#666}
.arrows{left:1024px;top:1705px;display:flex}
.arrows span{width:31px;height:29px;display:flex;align-items:center;justify-content:center}
.avatar{left:619px;top:1854px;width:64px;height:64px;border-radius:50%;background:linear-gradient(135deg,#c98b6e,#7d3f30)}
.author{left:696px;top:1874px;font-size:14px;color:#444}

.footer{left:0;top:2021px;width:1200px;height:317px;background:var(--footer);color:#ddd}
.follow{left:116px;top:2005px;width:261px;height:48px;background:var(--orange);display:flex;align-items:center;padding-left:22px;gap:11px;color:#333;font-size:14px;font-weight:600}
.follow::before{content:"";position:absolute;left:-10px;top:0;border-right:10px solid #b24e12;border-top:16px solid transparent}
.follow .social{width:24px;height:24px;background:rgba(255,255,255,.85)}
.follow .social:first-of-type{margin-left:8px}
.fcol{top:2076px}
.fcol h5{font-size:16px;font-weight:600;color:#fff;margin-bottom:20px}
.fcol p{font-size:11px;line-height:20px;color:#ddd}
.links li{list-style:none;font-size:11.5px;margin-bottom:21px;display:flex;gap:18px;color:#eee}
.links li::before{content:"›";color:var(--orange)}
.contact-row{display:flex;gap:11px;font-size:12px;line-height:20px;margin-bottom:18px;color:#eee}
.hours{font-size:11.5px;color:#eee}
.hours div{display:flex;margin-top:23px}
.hours span:first-child{width:100px}
.copyright{left:0;top:2338px;width:1200px;height:40px;background:var(--footer-base);color:#ddd;font-size:11px;text-align:center;line-height:40px}
</style>
</head>
<body>

<div class="abs topbar">
  <div class="item" style="left:120px">
    <svg width="13" height="10" viewBox="0 0 13 10"><rect x=".5" y=".5" width="12" height="9" fill="none" stroke="#eee"/><path d="M.5 .5 6.5 5.5 12.5 .5" fill="none" stroke="#eee"/></svg>
    info@birchhollow.test
  </div>
  <div class="item" style="left:290px">
    <svg width="11" height="11" viewBox="0 0 24 24"><path fill="#eee" d="M6.6 10.8a15 15 0 0 0 6.6 6.6l2.2-2.2c.3-.3.7-.4 1-.2 1.1.4 2.3.6 3.6.6.6 0 1 .4 1 1V20c0 .6-.4 1-1 1A17 17 0 0 1 3 4c0-.6.4-1 1-1h3.5c.6 0 1 .4 1 1 0 1.3.2 2.5.6 3.6.1.3 0 .7-.2 1z"/></svg>
    1-800 555 0142
  </div>
  <div class="item" style="left:722px">
    <svg width="10" height="13" viewBox="0 0 10 13"><path fill="#eee" d="M5 0a5 5 0 0 0-5 5c0 3.5 5 8 5 8s5-4.5 5-8a5 5 0 0 0-5-5zm0 7a2 2 0 1 1 0-4 2 2 0 0 1 0 4z"/></svg>
    410 Prairie Lane, Amarillo, TX 79101
  </div>
  <div class="search">
    <svg width="14" height="14" viewBox="0 0 14 14"><circle cx="6" cy="6" r="4.5" fill="none" stroke="#fff" stroke-width="2"/><path d="M9.3 9.3 13 13" stroke="#fff" stroke-width="2"/></svg>
  </div>
</div>

<header class="abs header">
  <div class="logo">
    <div class="name">BIRCH HOLLOW</div>
    <div class="sub">HOMES</div>
  </div>
  <nav class="nav">
    <a class="active">Home</a>
    <a>Available homes</a>
    <a>Available floor plans</a>
    <a>Guide to ownership</a>
    <a>Contact</a>
  </nav>
</header>

<section class="abs hero" role="img" aria-label="Architectural sketch of a two-storey house drawn over blueprint plans"></section>
<div class="abs play"><svg width="56" height="56" viewBox="0 0 56 56"><path d="M23 18 37 28 23 38z" fill="#fff"/></svg></div>
<div class="abs caption">Virtual Tours of the Homes</div>

<h2 class="abs section-title" style="top:580px"><b>Welcome To</b> Birch Hollow Homes</h2>
<p class="abs intro">Sed ut perspiciatis unde omnis iste natus error sit voluptatem accusantium doloremque laudantium, totam rem aperiam, eaque ipsa quae ab illo inventore veritatis et quasi architecto beatae vitae dicta sunt explicabo. Nemo enim ipsam voluptatem quia voluptas sit aspernatur aut odit aut fugit, sed quia consequuntur magni dolores eos qui ratione voluptatem sequi nesciunt.</p>
<a class="abs btn" style="left:553px;top:719px;width:95px;height:32px;line-height:30px">Read more</a>

<h2 class="abs section-title" style="top:771px"><b>Our</b> Services</h2>

<article class="abs service" style="left:132px">
  <div class="media" role="img" aria-label="Sketch of a modern two-storey house with timber screens" style="background:linear-gradient(135deg,#f7f7f7,#e3e3e3 60%,#d8c7b2)"></div>
  <h3>Available <span>Homes</span></h3>
  <svg class="arrow" width="18" height="12" viewBox="0 0 18 12"><path d="M0 6h16M11 1l5 5-5 5" fill="none" stroke="var(--orange)" stroke-width="1.6"/></svg>
  <p>Duis aute irure dolor in reprehenderit in voluptate velit esse cillum dolore eu fugiat nulla pariatur.</p>
</article>
<article class="abs service" style="left:618px">
  <div class="media" role="img" aria-label="Cutaway 3D floor plan of a furnished home on blueprints" style="background:linear-gradient(135deg,#dcdcdc,#b49a80 55%,#8a6f58)"></div>
  <h3>Floor <span>Plans</span></h3>
  <svg class="arrow" width="18" height="12" viewBox="0 0 18 12"><path d="M0 6h16M11 1l5 5-5 5" fill="none" stroke="var(--orange)" stroke-width="1.6"/></svg>
  <p>Duis aute irure dolor in reprehenderit in voluptate velit esse cillum dolore eu fugiat nulla pariatur.</p>
</article>

<section class="abs posts"></section>
<h2 class="abs section-title" style="top:1262px"><b>Latest</b> Posts</h2>

<article class="abs post" style="left:98px">
  <div class="media" role="img" aria-label="Model house resting on rolled building plans" style="background:linear-gradient(135deg,#e9eef2,#9fb0bd)"></div>
  <h4><b>FLOOR</b> PLANS</h4>
  <p>Sed ut perspiciatis unde omnis iste natus error sit voluptatem accusantium doloremque laudantium, totam rem aperiam, eaque ipsa quae...</p>
  <a class="btn solid">Read more</a>
</article>
<article class="abs post" style="left:437px">
  <div class="media" role="img" aria-label="Architect's hands working over drawings on a desk" style="background:linear-gradient(135deg,#e8e2d8,#c9a26a 60%,#8b5a2b)"></div>
  <h4><b>ARCHITECTURAL</b> DRAWINGS</h4>
  <p>Sed ut perspiciatis unde omnis iste natus error sit voluptatem accusantium doloremque laudantium, totam rem aperiam, eaque ipsa quae.....</p>
  <a class="btn">Read more</a>
</article>
<article class="abs post" style="left:777px">
  <div class="media" role="img" aria-label="Team reviewing house plans together at a table" style="background:linear-gradient(135deg,#8a7a70,#d9cfc4 60%,#6d7f95)"></div>
  <h4><b>FLOOR</b> PLANS</h4>
  <p>Sed ut perspiciatis unde omnis iste natus error sit voluptatem accusantium doloremque laudantium, totam rem aperiam, eaque ipsa quae...</p>
  <a class="btn">Read more</a>
</article>

<h2 class="abs block-title" style="left:124px;top:1697px"><b>Our</b> Clients</h2>
<div class="abs clients">
  <div class="client">Maple &amp; Co.</div>
  <div class="client">Fernwood</div>
  <div class="client"><span class="dot"></span>Ledgerline</div>
  <div class="client">Tickwell</div>
  <div class="client">Brightgrid</div>
  <div class="client">Northpoint</div>
</div>

<h2 class="abs block-title" style="left:631px;top:1697px;font-weight:600;color:#555">Testimonials</h2>
<div class="abs arrows">
  <span style="background:#bbb"><svg width="8" height="12" viewBox="0 0 8 12"><path d="M6 1 1 6l5 5" fill="none" stroke="#fff" stroke-width="1.6"/></svg></span>
  <span style="background:var(--orange)"><svg width="8" height="12" viewBox="0 0 8 12"><path d="M2 1l5 5-5 5" fill="none" stroke="#fff" stroke-width="1.6"/></svg></span>
</div>
<p class="abs testimonial">Dummy text is text that is used in the publishing industry or by web designers to occupy the space which will later be filled with 'real' content. This is required when, for example, the final text is not yet available.</p>
<div class="abs avatar" role="img" aria-label="Client portrait"></div>
<div class="abs author">Daniel R. Hayes</div>

<footer class="abs footer"></footer>
<div class="abs follow">Follow Us <span class="social"></span><span class="social"></span><span class="social"></span><span class="social"></span></div>

<div class="abs fcol" style="left:132px;width:270px">
  <h5>About Company</h5>
  <p>Lorem ipsum dolor sit amet, consectetur adipiscing elit, sed do eiusmod tempor incididunt ut labore et dolore magna aliqua. Ut enim ad minim veniam, quis nostrud exercitation ullamco laboris nisi ut aliquip ex ea commodo consequat.</p>
  <p style="margin-top:20px">Duis aute irure dolor in reprehenderit in voluptate velit esse cillum dolore eu fugiat nulla pariatur.</p>
</div>
<div class="abs fcol" style="left:441px">
  <h5>Quick Links</h5>
  <ul class="links"><li>Home</li><li>Services</li><li>Recent Projects</li><li>About Us</li><li>Contact Us</li></ul>
</div>
<div class="abs fcol" style="left:621px;width:220px">
  <h5>Contact Us</h5>
  <div class="contact-row"><svg width="12" height="16" viewBox="0 0 10 13"><path fill="var(--orange)" d="M5 0a5 5 0 0 0-5 5c0 3.5 5 8 5 8s5-4.5 5-8a5 5 0 0 0-5-5zm0 7a2 2 0 1 1 0-4 2 2 0 0 1 0 4z"/></svg><span>Main Office 2208 Canyon Dr,<br>Amarillo</span></div>
  <div class="contact-row"><svg width="12" height="12" viewBox="0 0 24 24"><path fill="var(--orange)" d="M6.6 10.8a15 15 0 0 0 6.6 6.6l2.2-2.2c.3-.3.7-.4 1-.2 1.1.4 2.3.6 3.6.6.6 0 1 .4 1 1V20c0 .6-.4 1-1 1A17 17 0 0 1 3 4c0-.6.4-1 1-1h3.5c.6 0 1 .4 1 1 0 1.3.2 2.5.6 3.6.1.3 0 .7-.2 1z"/></svg><span>(806)-555-0178</span></div>
  <div class="contact-row"><svg width="12" height="10" viewBox="0 0 13 10"><rect width="13" height="10" fill="var(--orange)"/><path d="M0 0 6.5 5.5 13 0" fill="none" stroke="#fff"/></svg><span>info@birchhollow.test</span></div>
</div>
<div class="abs fcol" style="left:870px;width:230px">
  <h5>Business Hours</h5>
  <p style="font-size:10.5px">Our support available to help you 24 hours a day, seven days a week.</p>
  <div class="hours">
    <div><span>Monday-Friday:</span><span>9am to 5pm</span></div>
    <div><span>Saturday:</span><span>10am to 2pm</span></div>
    <div><span>Sunday:</span><span>Closed</span></div>
  </div>
</div>

<div class="abs copyright">Copyrights © 2017 - All Rights Reserved</div>

</body>
</html>
```